Satchel & Sundial needs new business card design

I need a new business card design. I'm looking for out-of-the-box design which represents the freedom of being a location independent entrepreneur.
I offer coaching, retreats and trips.
I would like to see designs with and without the photo.
Colors I use are black (#000000), green (#25A796) and brown (#D7C38C)
Website satchelandsundial.example

Target Market(s)

location independent entrepreneurs, digital nomads, people looking to swap the 9 to 5 for a lifestyle business

Industry/Entity Type

Business

Contact Information for Business Card

Dorota Falkner
Your Lifestyle Business Coach, Retreat & Trip Leader
http://satchelandsundial.example
hello@satchelandsundial.example
Live a life you don't need a holiday from

Font styles to use
Serif
Sans Serif

Requirements
Must have
• One side should contain only the logo. I would also consider having the "Live a life you don't need a holiday from" on that side too (depending on how it looks)
• Please show both sides on the designs.

```html
<!DOCTYPE html>
<html lang="en">
<head>
<meta charset="utf-8">
<title>Satchel &amp; Sundial – Business Card</title>
<link rel="stylesheet" href="https://fonts.googleapis.com/css2?family=Open+Sans:ital,wght@0,400;0,600;0,700;1,400&display=swap">
<style>
  :root {
    --ink: #000000;
    --band: #231f20;
    --green: #25a796;
    --text: #2b2b2b;
    --muted: #555555;
    --paper: #ffffff;
    --backdrop: #9b9b9b;
    --pattern-light: #f3f3f3;
    --pattern-mid: #e6e6e6;
  }
  * { box-sizing: border-box; margin: 0; padding: 0; }
  html, body {
    width: 1105px; height: 1200px; overflow: hidden;
    background: var(--backdrop);
    font-family: "Open Sans", Arial, sans-serif;
  }
  .card {
    position: absolute; left: 196px; width: 721px; height: 413px;
    background: var(--paper); overflow: hidden;
  }
  .card--front { top: 145px; }
  .card--back { top: 601px; }

  .band { position: absolute; left: 0; width: 100%; background: var(--band); }
  .band--top { top: 0; height: 18px; }
  .band--bottom { bottom: 0; height: 25px; }
  .stripe { position: absolute; }
  .stripe--top { top: 21px; left: 0; }
  .stripe--bottom { top: 370px; right: 0; }

  .wordmark {
    position: absolute; left: 0; width: 100%; text-align: center;
    font-weight: 700; color: var(--ink); letter-spacing: 1px; text-transform: uppercase;
  }
  .card--front .wordmark { top: 128px; font-size: 40px; }
  .card--back .wordmark { top: 158px; font-size: 56px; }

  .holder {
    position: absolute; top: 236px; width: 100%; text-align: center;
    color: var(--green); font-weight: 700; font-size: 23px; letter-spacing: 0.5px;
  }
  .role {
    position: absolute; top: 268px; width: 100%; text-align: center;
    color: var(--text); font-size: 19px;
  }
  .contacts {
    position: absolute; top: 299px; width: 100%;
    display: flex; justify-content: center; gap: 10px;
    font-size: 17.5px; color: var(--muted);
  }
  .contacts span { display: flex; align-items: center; gap: 5px; }
  .contacts svg { width: 16px; height: 16px; }

  .pattern {
    position: absolute; inset: 0;
    background: linear-gradient(160deg, var(--pattern-light), var(--pattern-mid) 50%, var(--pattern-light));
  }
  .socials { position: absolute; top: 25px; right: 24px; display: flex; gap: 4px; }
  .socials i { display: block; width: 26px; height: 26px; background: var(--green); }
  .tagline {
    position: absolute; top: 355px; width: 100%; text-align: center;
    font-style: italic; font-size: 18px; color: var(--text);
  }
</style>
</head>
<body>
  <section class="card card--front" aria-label="Card front">
    <div class="band band--top"></div>
    <svg class="stripe stripe--top" width="356" height="18" viewBox="0 0 356 18"><polygon points="0,0 356,0 338,18 0,18" fill="var(--green)"/></svg>
    <h1 class="wordmark">Satchel &amp; Sundial</h1>
    <p class="holder">DOROTA FALKNER</p>
    <p class="role">Your Lifestyle Business Coach, Retreat &amp; Trip Leader</p>
    <p class="contacts">
      <span><svg viewBox="0 0 16 16"><rect x="1" y="3" width="14" height="10" fill="var(--green)"/><polyline points="1,3 8,9 15,3" fill="none" stroke="#fff" stroke-width="1.3"/></svg>hello@satchelandsundial.example</span>
      <span><svg viewBox="0 0 16 16"><circle cx="8" cy="8" r="7" fill="var(--green)"/><path d="M1 8h14M8 1c3 3 3 11 0 14M8 1c-3 3-3 11 0 14" fill="none" stroke="#fff" stroke-width="1"/></svg>www.satchelandsundial.example</span>
    </p>
    <svg class="stripe stripe--bottom" width="356" height="18" viewBox="0 0 356 18"><polygon points="18,0 356,0 356,18 0,18" fill="var(--green)"/></svg>
    <div class="band band--bottom"></div>
  </section>

  <section class="card card--back" aria-label="Card back">
    <div class="pattern" role="img" aria-label="Faint repeated brand wordmark pattern across the card"></div>
    <div class="socials" aria-label="Social profiles"><i></i><i></i><i></i></div>
    <h2 class="wordmark">Satchel &amp; Sundial</h2>
    <p class="tagline">Live a life you don't need a holiday from</p>
  </section>
</body>
</html>
```